BOLD & MINIMALIST DESIGN NEEDED

We want a very bold but minimalistic business card design that is impactful and utilizes both sides of the business card. Our current logo is included for your use.

We want bold fonts and good use of negative space. We don't want the logo to overpower the design.

Target Market(s)

Professionals who are building new commercial buildings.

Industry/Entity Type

Construction

Contact Information for Business Card

Name, Title, email, office phone, cell phone, website

Font styles to use
Serif
Sans Serif

Requirements
Must have
• Bold design!

```html
<!DOCTYPE html>
<html lang="en">
<head>
<meta charset="utf-8">
<title>Crestmark Business Card</title>
<link href="https://fonts.googleapis.com/css2?family=Roboto:wght@400;700;900&display=swap" rel="stylesheet">
<style>
  :root {
    --bg: #e2e2e2;
    --paper: #f4f4f5;
    --ink: #0d0d0d;
    --text: #222222;
    --green: #7fba23;
    --green-light: #b3d97a;
    --rule: #2a2a2a;
  }
  * { box-sizing: border-box; margin: 0; padding: 0; }
  html, body {
    width: 1200px; height: 1040px; overflow: hidden;
    background: var(--bg);
    font-family: "Roboto", Arial, sans-serif;
  }
  .card {
    position: absolute; left: 220px;
    width: 760px; height: 435px;
    border-radius: 20px; overflow: hidden;
  }
  .card-front { top: 60px; background: var(--paper); }
  .card-back {
    top: 545px;
    background: radial-gradient(ellipse at 50% 40%, var(--green-light) 0%, var(--green) 75%);
  }
  .brand {
    position: absolute; right: 50px; top: 125px;
    display: flex; align-items: center; gap: 12px;
    font-weight: 900; font-size: 38px; letter-spacing: 0.5px;
    color: var(--ink);
  }
  .brand-square { width: 22px; height: 22px; background: var(--green); }
  .person { position: absolute; left: 54px; top: 245px; }
  .person-name { font-weight: 700; font-size: 30px; color: var(--ink); letter-spacing: 0.3px; }
  .person-title { font-size: 19px; color: var(--green); margin-top: 2px; }
  .divider {
    position: absolute; left: 54px; right: 50px; top: 303px;
    height: 1px; background: var(--rule);
  }
  .contact-list { position: absolute; left: 54px; top: 318px; list-style: none; }
  .contact-list li {
    display: flex; align-items: center; gap: 9px;
    font-size: 19px; color: var(--text); line-height: 24px;
  }
  .contact-list svg { width: 15px; height: 15px; fill: var(--ink); }
  .address {
    position: absolute; right: 50px; top: 320px;
    text-align: right; font-size: 19px; line-height: 25px; color: var(--text);
  }
  .band { position: absolute; left: 0; bottom: 0; width: 760px; height: 21px; }
  .back-brand {
    position: absolute; left: 0; right: 0; top: 155px;
    display: flex; justify-content: center; align-items: center; gap: 20px;
    font-weight: 900; font-size: 72px; color: var(--ink); letter-spacing: 1px;
  }
  .back-brand .brand-square { width: 40px; height: 40px; background: var(--ink); }
  .back-web {
    position: absolute; left: 0; right: 0; top: 378px;
    text-align: center; font-size: 19px; color: var(--text);
  }
</style>
</head>
<body>
  <section class="card card-front">
    <div class="brand"><span class="brand-square"></span>CRESTMARK</div>

    <div class="person">
      <div class="person-name">AARON KESSLER</div>
      <div class="person-title">President</div>
    </div>
    <div class="divider"></div>

    <ul class="contact-list">
      <li>
        <svg viewBox="0 0 16 16" aria-hidden="true"><path d="M3.6 1.2l2.3 2.6c.4.4.4 1 0 1.4L4.8 6.4c.9 2 2.5 3.6 4.6 4.6l1.2-1.1c.4-.4 1-.4 1.4 0l2.6 2.3c.4.4.4 1 0 1.4l-1.3 1.3C11.6 16.5 0 6 .9 2.5L2.2 1.2c.4-.4 1-.4 1.4 0z"/></svg>
        (555) 0142-7780
      </li>
      <li>
        <svg viewBox="0 0 16 16" aria-hidden="true"><path d="M1 3h14v10H1z M2.5 4.3v.3L8 8.6l5.5-4v-.3z" fill-rule="evenodd"/></svg>
        info@crestmarkbuild.com
      </li>
      <li>
        <svg viewBox="0 0 16 16" aria-hidden="true"><circle cx="8" cy="8" r="7.2"/><path d="M4 4.5c1.5.2 2.3 1.3 1.8 2.5-.5 1 .8 1.8.4 3.2L5 12.5C3 11 2.5 7 4 4.5zM10 3c1.3.8 1 2-.3 2.3-1 .3-.5 1.6.8 1.5 1.5-.1 2.5 1 2.2 2.6C12 6 11.5 4 10 3z" fill="#f4f4f5"/></svg>
        www.crestmarkbuild.com
      </li>
    </ul>

    <address class="address" style="font-style:normal">
      2190 Harrow Lane<br>
      Elm Ridge, NY 11990
    </address>

    <svg class="band" viewBox="0 0 760 21" preserveAspectRatio="none" aria-hidden="true">
      <defs>
        <linearGradient id="bandGreen" x1="0" x2="1" y1="0" y2="0">
          <stop offset="0" stop-color="#7fba23"/>
          <stop offset="1" stop-color="#b3d97a"/>
        </linearGradient>
      </defs>
      <polygon points="0,0 497,0 492,21 0,21" fill="#0d0d0d"/>
      <polygon points="503,0 760,0 760,21 498,21" fill="url(#bandGreen)"/>
    </svg>
  </section>

  <section class="card card-back">
    <div class="back-brand"><span class="brand-square"></span>CRESTMARK</div>
    <div class="back-web">www.crestmarkbuild.com</div>
  </section>
</body>
</html>
```